New Baby Formula Company Needs a Shopify Website Design

We are launching a baby formula company and need a Shopify website design. We have a patented product that is a disposable pouch with a frangible seal through the middle. The top half contains formula powder and the bottom half contains purified water. There is also a bottle nipple on the corner under the cap in order to feed the baby. You just need to squeeze the bottom half of the pouch to break the seal and then the water and formula will mix. You then only need to shake it and then remove the cap and feed the baby. We will also sell formula in containers like the other formula companies. We want this website to stand out and look professional. We don't want a boring layout, but something unique and captivating. I have attached a mockup rendering of our product, though it's not the finished product and our logo. This will let you know the color scheme we are going for. Let me know if you have any further questions. Thank you

```html
<!DOCTYPE html>
<html lang="en">
<head>
<meta charset="UTF-8">
<title>MilaBaby — Infant Formula</title>
<link rel="stylesheet" href="https://fonts.googleapis.com/css2?family=Lato:wght@400;700;900&display=swap">
<style>
:root{
  --green:#9fb12f;
  --green-dark:#8fa027;
  --cream:#fffff2;
  --pale:#f8fbe3;
  --ink:#1d1d1d;
  --white:#ffffff;
}
*{box-sizing:border-box;margin:0;padding:0}
html,body{width:1200px;height:4176px;overflow:hidden}
body{font-family:'Lato',sans-serif;color:var(--ink);background:var(--cream)}
.page{position:relative;width:1200px;height:4176px;overflow:hidden;background:var(--cream)}
.abs{position:absolute}

.topbar{left:0;top:0;width:1200px;height:42px;background:var(--green);color:var(--white);
  font-weight:700;font-size:19px;display:flex;align-items:center;justify-content:center;gap:10px}
.header{left:0;top:42px;width:1200px;height:102px;background:var(--cream)}
.brand{left:110px;top:56px;width:74px;height:74px;border:2px solid var(--green);border-radius:50%;
  display:flex;align-items:center;justify-content:center;color:var(--green);font-weight:700;font-size:15px}
.nav{left:405px;top:82px;display:flex;gap:31px;font-size:16px;font-weight:400;letter-spacing:.2px}
.nav span{white-space:nowrap}
.icon{top:82px;width:22px;height:22px}

.hero{left:0;top:144px;width:1200px;height:573px;
  background:linear-gradient(100deg,#eef0e2 0%,#d9d5c8 35%,#c9b6a6 60%,#e8e1da 85%,#f2efe8 100%)}
.hero-card{left:110px;top:240px;width:479px;height:355px;background:var(--cream);
  border:3px solid var(--green);border-radius:10px;box-shadow:0 10px 0 var(--green)}
.hero-title{left:36px;top:50px;font-size:43px;line-height:52px;font-weight:700;color:var(--green);letter-spacing:.5px}
.hero-text{left:36px;top:165px;width:395px;font-size:15.5px;line-height:28px}
.btn-outline{left:36px;top:240px;width:136px;height:50px;border:3px solid var(--green);border-radius:25px;
  color:var(--green);font-weight:700;font-size:16px;display:flex;align-items:center;justify-content:center;
  box-shadow:0 4px 0 var(--green)}

.section-title{font-size:36px;font-weight:700;color:var(--green);letter-spacing:.3px}
.product-card{background:var(--white);border:3px solid var(--green);border-radius:12px;box-shadow:0 6px 0 var(--green);overflow:hidden}
.pouch{position:absolute;border-radius:14px 14px 26px 26px;
  background:linear-gradient(180deg,#f4f4ee 0%,#f4f4ee 42%,#a3b537 58%,#93a62c 100%)}
.item-name{font-size:16px;font-weight:700;letter-spacing:.2px}
.item-price{font-size:16px;font-weight:700}

.products-band{left:0;top:1340px;width:1200px;height:1092px;background:var(--pale)}
.link{font-size:18px;font-weight:400;display:flex;align-items:center;gap:10px}

.touch{left:112px;top:2546px;width:978px;height:483px;border:3px solid var(--green);border-radius:10px;
  background:var(--cream);overflow:hidden;box-shadow:0 4px 0 var(--green)}
.touch-photo{left:0;top:0;width:491px;height:480px;border-right:2px solid var(--green);
  background:linear-gradient(135deg,#efe8df 0%,#d8c2a6 40%,#cfc6bd 70%,#9fb0c8 100%)}
.touch-title{left:525px;top:130px;font-size:38px;font-weight:700;color:var(--green)}
.touch-text{left:528px;top:196px;width:385px;font-size:15px;line-height:29px}
.btn-solid{left:528px;top:296px;width:151px;height:50px;border-radius:25px;background:var(--green);color:var(--white);
  font-weight:700;font-size:17px;display:flex;align-items:center;justify-content:center;box-shadow:0 4px 0 var(--green-dark)}

.newsletter{left:112px;top:3222px;width:981px;height:289px;border:3px solid var(--green);border-radius:26px;
  background:var(--white);box-shadow:0 4px 0 var(--green)}
.news-title{left:0;top:42px;width:100%;text-align:center;font-size:37px;font-weight:700;color:var(--green)}
.news-sub{left:0;top:106px;width:100%;text-align:center;font-size:17px}
.email{left:276px;top:157px;width:425px;height:75px;border:3px solid var(--green);border-radius:14px;
  box-shadow:0 4px 0 var(--green);display:flex;align-items:center;justify-content:space-between;padding:0 30px 0 36px;
  font-size:20px;font-weight:700}

.footer{left:0;top:3616px;width:1200px;height:560px;background:var(--green);color:var(--white)}
.foot-brand{left:155px;top:82px;width:130px;height:130px;border:3px solid var(--white);border-radius:50%;
  display:flex;align-items:center;justify-content:center;font-size:26px;font-weight:700}
.foot-head{font-size:26px;font-weight:700}
.foot-links{left:500px;top:128px;display:flex;flex-direction:column;gap:18px;font-size:17px}
.foot-mission{left:778px;top:130px;width:300px;font-size:15px;line-height:26px}
.social-row{left:0;top:340px;width:1200px;display:flex;justify-content:center;gap:26px}
.social{display:flex;align-items:center;gap:6px;font-size:14px;font-weight:700;color:var(--white)}
.social i{display:block;width:9px;height:9px;border-radius:50%;background:var(--white)}
.rule{left:110px;top:415px;width:977px;height:2px;background:var(--white)}
.pay-row{left:0;top:456px;width:1200px;display:flex;justify-content:center;gap:8px}
.pay{height:28px;padding:0 9px;border-radius:4px;background:var(--white);color:var(--green-dark);
  font-size:12px;font-weight:700;display:flex;align-items:center}
.copy{left:0;top:520px;width:100%;text-align:center;font-size:15px}
</style>
</head>
<body>
<div class="page">

  <div class="abs topbar">FREE Shipping Over $70 (USA Only)
    <svg width="16" height="16" viewBox="0 0 16 16"><path d="M3 13 L13 3 M8 3 H13 V8" stroke="#fff" stroke-width="2" fill="none"/></svg>
  </div>

  <div class="abs header"></div>
  <div class="abs brand">MilaBaby</div>
  <nav class="abs nav"><span>HOME</span><span>PURIFIED WATER</span><span>PRODUCTS</span><span>ABOUT</span><span>GIFT CARD</span></nav>
  <svg class="abs icon" style="left:1007px" viewBox="0 0 22 22"><rect x="4" y="7" width="14" height="13" fill="none" stroke="#222" stroke-width="1.6"/><path d="M8 9 V5 a3 3 0 0 1 6 0 V9" fill="none" stroke="#222" stroke-width="1.6"/></svg>
  <svg class="abs icon" style="left:1070px" viewBox="0 0 22 22"><circle cx="9" cy="9" r="5" fill="none" stroke="#222" stroke-width="1.8"/><path d="M13 13 L18 18" stroke="#222" stroke-width="1.8"/></svg>

  <div class="abs hero" role="img" aria-label="Photo of a mother kissing her baby while bottle feeding"></div>
  <div class="abs hero-card">
    <h1 class="abs hero-title">WELCOME TO<br>MILABABY</h1>
    <p class="abs hero-text">Itaque earum rerum hic tenetur a sapiente delectus, ut aut reicienoloribus asperiores repellat.</p>
    <div class="abs btn-outline">SHOP NOW</div>
  </div>

  <h2 class="abs section-title" style="left:109px;top:788px">BEST SELLERS</h2>

  <div class="abs product-card" style="left:109px;top:872px;width:276px;height:309px">
    <div class="pouch" role="img" aria-label="Formula pouch front view" style="left:56px;top:36px;width:154px;height:228px"></div>
  </div>
  <div class="abs product-card" style="left:462px;top:872px;width:276px;height:309px">
    <div class="pouch" role="img" aria-label="Formula pouch front view" style="left:48px;top:50px;width:176px;height:220px"></div>
  </div>
  <div class="abs product-card" style="left:812px;top:872px;width:276px;height:309px">
    <div class="pouch" role="img" aria-label="Formula pouch back view with nutrition facts" style="left:56px;top:46px;width:158px;height:220px"></div>
  </div>
  <div class="abs item-name" style="left:109px;top:1203px">LOREM IPSUM</div>
  <div class="abs item-price" style="left:109px;top:1237px">$ 02.95</div>
  <div class="abs item-name" style="left:471px;top:1203px">LOREM IPSUM</div>
  <div class="abs item-price" style="left:471px;top:1237px">$ 02.95</div>
  <div class="abs item-name" style="left:813px;top:1203px">LOREM IPSUM</div>
  <div class="abs item-price" style="left:813px;top:1237px">$ 02.95</div>

  <div class="abs products-band"></div>
  <h2 class="abs section-title" style="left:112px;top:1435px">OUR PRODUCTS</h2>

  <div class="abs product-card" style="left:112px;top:1540px;width:310px;height:325px">
    <div class="pouch" role="img" aria-label="Formula pouch front view" style="left:60px;top:60px;width:188px;height:222px"></div>
  </div>
  <div class="abs product-card" style="left:112px;top:1959px;width:310px;height:325px">
    <div class="pouch" role="img" aria-label="Formula pouch back view with nutrition facts" style="left:72px;top:44px;width:168px;height:228px"></div>
  </div>
  <div class="abs product-card" style="left:439px;top:1540px;width:651px;height:744px">
    <div class="pouch" role="img" aria-label="Large formula pouch with cap and feeding spout" style="left:145px;top:130px;width:340px;height:520px"></div>
  </div>
  <div class="abs link" style="left:112px;top:1895px">Lorem Ipsum
    <svg width="18" height="14" viewBox="0 0 18 14"><path d="M1 7 H16 M10 1 L16 7 L10 13" stroke="#1d1d1d" stroke-width="2" fill="none"/></svg></div>
  <div class="abs link" style="left:112px;top:2313px">Lorem Ipsum
    <svg width="18" height="14" viewBox="0 0 18 14"><path d="M1 7 H16 M10 1 L16 7 L10 13" stroke="#1d1d1d" stroke-width="2" fill="none"/></svg></div>
  <div class="abs link" style="left:439px;top:2313px">Lorem Ipsum
    <svg width="18" height="14" viewBox="0 0 18 14"><path d="M1 7 H16 M10 1 L16 7 L10 13" stroke="#1d1d1d" stroke-width="2" fill="none"/></svg></div>

  <div class="abs touch">
    <div class="abs touch-photo" role="img" aria-label="Photo of a mother feeding her baby on a bed"></div>
    <h2 class="abs touch-title">GET IN TOUCH WITH US</h2>
    <p class="abs touch-text">Temporibus autem quibusdam et aut officiis debitis aut rerum necessitatibus saepe eveniet ut et voluptates repudiandae sint et molestiae non recusandae.</p>
    <div class="abs btn-solid">SHOP NOW</div>
  </div>

  <div class="abs newsletter">
    <h2 class="abs news-title">JOIN OUR NEWSLETTER</h2>
    <p class="abs news-sub">Itaque earum rerum hic tenetur</p>
    <div class="abs email">Email
      <svg width="24" height="18" viewBox="0 0 24 18"><path d="M1 9 H21 M13 1 L21 9 L13 17" stroke="#1d1d1d" stroke-width="2.4" fill="none"/></svg></div>
  </div>

  <footer class="abs footer">
    <div class="abs foot-brand">MilaBaby</div>
    <h3 class="abs foot-head" style="left:495px;top:78px">Quick Links</h3>
    <div class="abs foot-links"><span>Shop All</span><span>Our Product</span><span>Gift Card</span><span>Contact us</span></div>
    <h3 class="abs foot-head" style="left:778px;top:78px">Our Mission</h3>
    <p class="abs foot-mission">Itaque earum rerum hic tenetur a sapiente delectus, ut aut reiciendis voluptatibus maiores alias consequatur aut perferendis doloribus asperiores repellat.</p>
    <div class="abs social-row">
      <span class="social"><i></i>Facelane</span>
      <span class="social"><i></i>Workdeck</span>
      <span class="social"><i></i>Photoloop</span>
      <span class="social"><i></i>Clipcast</span>
    </div>
    <div class="abs rule"></div>
    <div class="abs pay-row">
      <span class="pay">Kardo</span>
      <span class="pay">Findly</span>
      <span class="pay">Amerix</span>
      <span class="pay">Vexa</span>
    </div>
    <p class="abs copy">2024@MilaBaby.All Rights Reserved</p>
  </footer>

</div>
</body>
</html>
```